Business card design for holistic health care clinic

We need a double-sided business card design for our holistic health care clinic that integrates our logo design and also its color scheme. My business is called Valmira. It is an integrative medicine clinic. You have already done the logo for me. Please ensure an elegant and upscale design that is not cluttered, but still has all the necessary information (please see below for details).

Target Market(s)

Wellness, fitness, rehabilitation for educated, well-traveled open-minded clients who are focused on natural, organic, balanced and preventive healthcare and lifestyle.

Industry/Entity Type

Medical

Contact Information for Business Card

Modern, clean.

Number of Pages Required

1 page

Font styles to use
Serif
Sans Serif

Colors

Designer to choose colors to be used in the design.

Requirements
Must have
• Logo on one side, all other information on the other side.
• Other information should include:
• Tobias Wrenfeld - DOE, CPT, LMT
• 4100 East Marrow Drive
• Austin, TX 78119
• 512 555 0148
• 818 555 0192
• info@ValmiraHealth.example
• t.wrenfeld@ValmiraHealth.example
Nice to have
• Darker background on front - but not totally black - shaded/dark gray.

```html
<!DOCTYPE html>
<html lang="en">
<head>
<meta charset="utf-8">
<title>Valmira — Business Card</title>
<link href="https://fonts.googleapis.com/css2?family=Source+Sans+3:ital,wght@0,400;0,600;1,400&display=swap" rel="stylesheet">
<style>
  :root {
    --page: #e9e7e3;
    --card-dark: #333436;
    --card-dark-edge: #2a2b2d;
    --brand-blue: #1a9ad6;
    --card-blue: #1496d3;
    --text-light: #e6e6e6;
    --rule: #8a8b8d;
    --white: #ffffff;
  }
  * { box-sizing: border-box; margin: 0; padding: 0; }
  html, body { width: 1200px; height: 911px; overflow: hidden; }
  body {
    background: var(--page);
    font-family: "Source Sans 3", "Helvetica Neue", Arial, sans-serif;
    position: relative;
  }
  .card {
    position: absolute;
    top: 300px;
    width: 540px;
    height: 310px;
    border-radius: 18px;
    overflow: hidden;
    box-shadow: 0 10px 26px rgba(0,0,0,0.22);
  }
  .card--front {
    left: 40px;
    background: linear-gradient(135deg, #3b3c3e 0%, var(--card-dark) 55%, var(--card-dark-edge) 100%);
    color: var(--text-light);
  }
  .card--back {
    left: 620px;
    background: var(--card-blue);
    color: var(--white);
  }

  /* Front: brand block */
  .brand {
    position: absolute;
    top: 38px;
    left: 44px;
    color: var(--brand-blue);
  }
  .brand__name {
    display: flex;
    align-items: center;
    gap: 10px;
    font-weight: 600;
    font-size: 46px;
    letter-spacing: 1px;
    line-height: 1;
    text-transform: uppercase;
  }
  .brand__dot {
    width: 14px; height: 14px; border-radius: 50%;
    background: var(--brand-blue);
  }
  .brand__tagline {
    margin-top: 4px;
    margin-left: 24px;
    font-size: 17px;
    font-weight: 400;
    letter-spacing: 0.3px;
  }

  /* Front: contact block */
  .contact {
    position: absolute;
    left: 44px;
    bottom: 30px;
    display: grid;
    grid-template-columns: 26px 1fr;
    column-gap: 18px;
    align-items: start;
  }
  .contact__icons {
    display: flex;
    flex-direction: column;
    gap: 0;
    padding-top: 2px;
  }
  .contact__icons svg { display: block; fill: var(--brand-blue); }
  .contact__name {
    color: var(--brand-blue);
    font-size: 19px;
    font-weight: 400;
    text-transform: uppercase;
    letter-spacing: 0.5px;
    padding-bottom: 6px;
    border-bottom: 1px solid var(--rule);
    margin-bottom: 8px;
  }
  .contact__creds { font-size: 12px; letter-spacing: 0.5px; }
  .contact__line { font-size: 14.5px; line-height: 18px; }
  .contact__group + .contact__group { margin-top: 6px; }
  .icon-slot { height: 36px; display: flex; align-items: center; justify-content: center; }
  .icon-slot--small { height: 18px; }

  /* Back */
  .back-brand {
    position: absolute;
    left: 60px;
    top: 50%;
    transform: translateY(-50%);
    display: flex;
    align-items: center;
    gap: 14px;
    font-weight: 600;
    font-size: 58px;
    letter-spacing: 2px;
    text-transform: uppercase;
    line-height: 1;
  }
  .back-brand__square { width: 22px; height: 22px; background: var(--white); }
  .back-tagline {
    position: absolute;
    right: 40px;
    top: 34px;
    font-style: italic;
    font-size: 17px;
    letter-spacing: 0.3px;
  }
</style>
</head>
<body>

<section class="card card--front" aria-label="Card front">
  <div class="brand">
    <div class="brand__name"><span class="brand__dot"></span>Valmira</div>
    <div class="brand__tagline">Integrative Holistic Medicine</div>
  </div>

  <div class="contact">
    <div class="contact__icons">
      <div class="icon-slot" aria-hidden="true">
        <svg width="16" height="16" viewBox="0 0 16 16"><circle cx="8" cy="4.5" r="3.5"/><path d="M1 16c0-4 3-6.5 7-6.5s7 2.5 7 6.5z"/></svg>
      </div>
      <div class="icon-slot" aria-hidden="true">
        <svg width="14" height="18" viewBox="0 0 14 18"><path d="M7 0a7 7 0 0 0-7 7c0 5 7 11 7 11s7-6 7-11a7 7 0 0 0-7-7zm0 9.5A2.5 2.5 0 1 1 7 4.5a2.5 2.5 0 0 1 0 5z"/></svg>
      </div>
      <div class="icon-slot icon-slot--small" aria-hidden="true">
        <svg width="14" height="14" viewBox="0 0 14 14"><path d="M3 0l2 3.5-1.5 1.5a8 8 0 0 0 5.5 5.5L10.5 9 14 11l-1 3C6 14 0 8 0 1z"/></svg>
      </div>
      <div class="icon-slot icon-slot--small" aria-hidden="true">
        <svg width="10" height="15" viewBox="0 0 10 15"><path d="M1.5 0h7A1.5 1.5 0 0 1 10 1.5v12A1.5 1.5 0 0 1 8.5 15h-7A1.5 1.5 0 0 1 0 13.5v-12A1.5 1.5 0 0 1 1.5 0zM1.5 2v10h7V2z"/></svg>
      </div>
      <div class="icon-slot icon-slot--small" aria-hidden="true">
        <svg width="15" height="11" viewBox="0 0 15 11"><path d="M0 0h15v11H0zM1.5 1.5l6 4.5 6-4.5z" fill-rule="evenodd"/></svg>
      </div>
      <div class="icon-slot icon-slot--small" aria-hidden="true">
        <svg width="14" height="14" viewBox="0 0 14 14"><circle cx="7" cy="7" r="6" fill="none" stroke="#1a9ad6" stroke-width="1.6"/><path d="M1 7h12M7 1c-3 3.5-3 8.5 0 12M7 1c3 3.5 3 8.5 0 12" fill="none" stroke="#1a9ad6" stroke-width="1.2"/></svg>
      </div>
    </div>

    <div class="contact__details">
      <div class="contact__name">Tobias Wrenfeld <span class="contact__creds">- DOE, CPT, LMT</span></div>
      <div class="contact__group">
        <div class="contact__line">4100 East Marrow Drive</div>
        <div class="contact__line">Austin, TX 78119</div>
      </div>
      <div class="contact__group">
        <div class="contact__line">512 555 0148</div>
        <div class="contact__line">818 555 0192</div>
        <div class="contact__line">t.wrenfeld@ValmiraHealth.example</div>
        <div class="contact__line">www.ValmiraHealth.example</div>
      </div>
    </div>
  </div>
</section>

<section class="card card--back" aria-label="Card back">
  <div class="back-brand"><span class="back-brand__square"></span>Valmira</div>
  <div class="back-tagline">helping the body help itself</div>
</section>

</body>
</html>
```